Coastal Learner Bureau business cards

Australian company about to start offering its services. We recruit international students to come to study English, vocational education and postgraduate courses in Australia. We help them find the institution and select the right city they want to come to Australia. We are a young, online oriented and supportive agency. Our clients are between 18 and 35 years old, mainly University students, young professionals or people with work experience. We provide much more information that any other agency offer. We administrate a Facebook group with more than 11.000 members that daily ask questions about general information when coming to Australia, while they are here and even after they leave the country

Target Market(s)

International students from South America, Central America and Europe

Industry/Entity Type

Student

Contact Information for Business Card

Tomas Bilbrea
Managing Director
tomas@kelvarin.com.au
www.kelvoria.com.au
+61 491058264
Melbourne, Australia

Font styles to use
Serif
Sans Serif

Colors

Designer to choose colors to be used in the design.

Requirements
Must have
• Horizontal design
• Standard business card size and shape. If font uses green or yellow colours, they will have to match the ones from the logo
Nice to have
• UPDATE: Use the contents of the green image to design one of the card sides. Use our logo in the background of that side as watermark.
• Passport image, or immigration stamps. A picture of the Yarra River (from Melbourne) would be cool as well.
Should not have
• Non-standard business card size and shape
• Not black as the background colour of any sides as we are not a VIP agency or a hight class service. We are orientes to young people and they like colours, pictures, something attractive.
• Vertical design
• NO YELLOW or BLACK AS THE BACKGROUND COLOUR OF ANY SIDE OF THE BIZ CARD

```html
<!DOCTYPE html>
<html lang="en">
<head>
<meta charset="utf-8">
<title>Coastal Learner Bureau – Business Card</title>
<link rel="stylesheet" href="https://fonts.googleapis.com/css2?family=EB+Garamond:ital,wght@0,400;0,700;1,400&display=swap">
<style>
  :root {
    --card-edge: #ffffff;
    --card-ground: #0c1e10;
    --accent-green: #2cb51c;
    --accent-lime: #c9dc00;
    --text-light: #ffffff;
  }
  * { margin: 0; padding: 0; box-sizing: border-box; }
  html, body {
    width: 1200px;
    height: 686px;
    overflow: hidden;
    background: var(--card-edge);
  }
  .card {
    position: relative;
    width: 1200px;
    height: 686px;
    background: var(--card-edge);
    font-family: "EB Garamond", Garamond, Georgia, serif;
    color: var(--text-light);
  }
  .card__ground {
    position: absolute;
    left: 14px;
    top: 11px;
    width: 1175px;
    height: 663px;
    background: var(--card-ground);
  }
  .card__side-bar {
    position: absolute;
    left: 0;
    top: 0;
    width: 14px;
    height: 686px;
    background: var(--accent-green);
  }
  .card__tab {
    position: absolute;
    background: var(--accent-lime);
  }
  .card__tab--top-right {
    left: 1145px;
    top: 11px;
    width: 46px;
    height: 154px;
  }
  .card__tab--bottom-left {
    left: 14px;
    top: 521px;
    width: 39px;
    height: 165px;
  }
  .identity {
    position: absolute;
    left: 317px;
    top: 0;
    width: 600px;
    text-align: center;
  }
  .identity__name {
    position: absolute;
    left: 0;
    width: 100%;
    top: 158px;
    font-size: 68px;
    font-weight: 700;
    line-height: 1;
    letter-spacing: 0.2px;
  }
  .identity__role {
    position: absolute;
    left: 0;
    width: 100%;
    top: 257px;
    font-size: 42px;
    font-weight: 700;
    line-height: 1;
  }
  .identity__rule {
    position: absolute;
    left: 28px;
    top: 327px;
    width: 549px;
    height: 4px;
    background: var(--accent-lime);
  }
  .contact {
    position: absolute;
    left: 0;
    width: 100%;
    top: 350px;
    list-style: none;
    font-style: italic;
    font-size: 32px;
    line-height: 43px;
  }
</style>
</head>
<body>
  <div class="card">
    <div class="card__ground"></div>
    <div class="card__side-bar"></div>
    <div class="card__tab card__tab--top-right"></div>
    <div class="card__tab card__tab--bottom-left"></div>

    <div class="identity">
      <h1 class="identity__name">Tomas Bilbrea</h1>
      <p class="identity__role">Managing Director</p>
      <div class="identity__rule"></div>
      <ul class="contact">
        <li class="contact__email">email: tomas@kelvarin.com.au</li>
        <li class="contact__phone">Tel: +61 491058264</li>
        <li class="contact__city">Melbourne, Australia</li>
        <li class="contact__web">web: www.kelvoria.com.au</li>
      </ul>
    </div>
  </div>
</body>
</html>
```